Create a wordpress website for Tovarin business solution

This project is to create a complete website with all pages.

Overview
The purpose of this project is to create a full complete website with all pages (16 pages). The site should be professional and modern. The site is for an IT recruiting and IT training company. The site needs to be easy to administer and update content. It should be simple to add pages, videos and testimonials later. I will leave the site layout, color schemes and flow to the designers.

Navigation Menu (Home, who we are, what we do, what makes us different, why it matters, candidate portal, contact us, Blog)

WHO WE ARE should be a drop down menu with link to pages (about us, mission, vision and purpose, our team)

WHAT WE DO should be drop down menu with link to the following pages (IT Recruiting, IT Training, Hardware and software sales)

What makes us different should be single page with different paragraph titles. (We live what we do, we don't compromise quality, we share knowledge, staffing guarantee)

Why it matters should be single page with paragraph titles. (Quickly fill positions, candidate career development)

Candidate portal should links to my portal login page. I can add the correct URL later. I just need it to link to somewhere. I can change it.

Contact us should have (address, phone number, google map and a form to submit request for a call back)

Blog - This link should launch a wordpress blogging module

Target Market(s)

IT RECRUITING AND CONSULTING

Industry/Entity Type

It Company

Coding

Coded - Design and coding required

Requirements
Must have
• Company Logo
• Navigation Menu (Home, who we are, what we do, what makes us different, why it matters, candidate portal, contact us)
• WHO WE ARE should be a drop down menu with link to pages (about us, mission, vision and purpose, our team)
• WHAT WE DO should be drop down menu with link to the following pages (IT Recruiting, IT Training, Hardware and software sales)
• What makes us different should be single page with different paragraph titles. (We live what we do, we don't compromise quality, we share knowledge, staffing guarantee)
• Why it matters should be single page with paragraph titles. (Quickly fill positions, candidate career development)
• Candidate portal should links to my portal login page. I can add the correct URL later. I just need it to link to somewhere. I can change it.
• Contact us should have (address, phone number, google map and a form to submit request for a call back)

```html
<!DOCTYPE html>
<html lang="en">
<head>
<meta charset="utf-8">
<title>Tovarin Business Solution</title>
<link rel="stylesheet" href="https://fonts.googleapis.com/css2?family=Roboto:wght@400;500;700&display=swap">
<style>
:root{
  --blue:#0b5ca0;
  --blue-dark:#0a4f8c;
  --navy:#0e4a86;
  --orange:#e0661a;
  --text:#333;
  --muted:#666;
  --line:#d7d7d7;
  --grey-bg:#e6e6e6;
  --footer-bg:#ececec;
  --white:#fff;
}
*{box-sizing:border-box;margin:0;padding:0}
html,body{width:1200px;height:2579px;overflow:hidden}
body{font-family:"Roboto",Arial,sans-serif;color:var(--text);background:var(--white);position:relative}
.abs{position:absolute}

/* header */
.brand{left:88px;top:48px;font-size:40px;font-weight:500;color:var(--blue);letter-spacing:.5px}
.contact-chip{top:46px;display:flex;align-items:center;gap:16px}
.chip-icon{width:46px;height:46px;border:2px solid var(--orange);border-radius:50%;display:flex;align-items:center;justify-content:center}
.chip-label{font-size:13px;color:var(--orange);text-transform:uppercase}
.chip-value{font-size:14px;font-weight:700;color:var(--blue);margin-top:4px}

/* nav */
.main-nav{left:0;top:134px;width:1200px;height:50px;border-top:1px solid var(--line);border-bottom:1px solid var(--line);border-left:1px solid var(--line);border-right:1px solid var(--line);display:flex;align-items:center;padding-left:86px;gap:37px}
.main-nav a{font-size:14px;font-weight:500;color:#222;text-decoration:none;text-transform:uppercase;position:relative;height:50px;line-height:50px}
.main-nav a.active{color:#222}
.main-nav a.active::after{content:"";position:absolute;left:0;right:0;bottom:-1px;height:3px;background:var(--orange)}

/* hero */
.hero{left:0;top:184px;width:1200px;height:474px;background:linear-gradient(100deg,#0b4f8f 0%,#0d5a9c 55%,#194f86 75%,#0d4d8a 100%)}
.hero-title-box{left:86px;top:292px;width:524px;height:117px;background:rgba(255,255,255,.2);clip-path:polygon(0 0,100% 0,94% 100%,0 100%)}
.hero-title{left:123px;top:310px;font-size:31px;font-weight:500;color:var(--white);text-transform:uppercase}
.hero-sub{left:124px;top:353px;font-size:19px;color:var(--white)}
.hero-chevron{left:323px;top:388px;width:42px;height:42px;border-radius:50%;background:#9fb6cc;display:flex;align-items:center;justify-content:center}

.feature-photo{border-radius:50%;border:6px solid #eef2f6;box-shadow:0 10px 24px rgba(0,0,0,.25)}
.feature-photo.highlight{border-color:var(--orange)}
.mouse{width:22px;height:36px}

.feature-caption{text-align:center;width:280px}
.feature-caption .kicker{font-size:16px;color:var(--orange)}
.feature-caption .title{font-size:20px;font-weight:500;color:var(--navy);margin-top:14px;text-transform:uppercase}

/* stats */
.stats{left:0;top:923px;width:1200px;height:249px;background:linear-gradient(90deg,#0b5a9f,#0d5fa5 50%,#0b5a9f)}
.stat{width:140px;text-align:center;color:var(--white)}
.stat svg{display:block;margin:0 auto}
.stat .num{font-size:22px;font-weight:700;margin-top:18px}
.stat .label{font-size:17px;margin-top:4px}

/* blog */
.blog{left:0;top:1172px;width:1200px;height:647px;background:var(--grey-bg)}
.section-kicker{font-size:16px;color:var(--orange)}
.section-title{font-size:24px;font-weight:700;color:var(--navy);text-transform:uppercase}
.blog-card{top:1341px;width:311px;height:400px;background:var(--white);border-radius:6px;box-shadow:0 2px 6px rgba(0,0,0,.12);padding:9px}
.blog-photo{height:263px;border:2px solid var(--blue);border-radius:6px}
.blog-head{display:flex;justify-content:space-between;align-items:baseline;margin:20px 8px 0}
.blog-head h3{font-size:16px;font-weight:500;color:#222;text-transform:uppercase}
.blog-head time{font-size:12px;font-style:italic;color:var(--orange)}
.blog-card p{font-size:12.5px;line-height:18px;color:var(--muted);margin:8px 8px 0}
.read-more{display:block;font-size:12.5px;font-weight:700;color:var(--blue);margin:6px 8px 0;text-decoration:none}

/* callback */
.field{height:38px;border:1px solid #c9c9c9;background:var(--white);font-size:12.5px;color:#888;padding:0 10px;display:flex;align-items:center}
.field.select{border-color:#555;color:#333;justify-content:space-between}
.btn{background:var(--orange);color:var(--white);font-size:13px;font-weight:700;text-transform:uppercase;display:flex;align-items:center;justify-content:center;border-radius:2px}
.phone-box{left:626px;top:1994px;width:271px;height:96px;border:1px solid var(--orange);display:flex;align-items:center;padding-left:40px;gap:28px;background:var(--white)}
.phone-box .small{font-size:12px;color:#444}
.phone-box .big{font-size:25px;font-weight:700;color:var(--orange);margin-top:4px}
.hours{left:626px;top:2105px;font-size:15px;font-weight:700;color:#111}
.hours span{color:var(--orange);font-weight:400}
.hours em{font-style:normal;font-weight:400;color:#333}

/* footer */
.footer{left:0;top:2209px;width:1200px;height:370px;background:linear-gradient(180deg,#efefef,#e8e8e8)}
.footer h4{font-size:19px;font-weight:500;color:#222;text-transform:uppercase}
.touch-item{display:flex;gap:14px;align-items:flex-start}
.touch-icon{width:36px;height:36px;border:1px solid #9aa9b8;border-radius:50%;display:flex;align-items:center;justify-content:center;flex-shrink:0}
.touch-text{font-size:13px;color:#666;line-height:18px}
.touch-text strong{display:block;color:var(--blue);font-weight:700}
.link-list{list-style:none}
.link-list li{font-size:13px;color:#555;height:22.3px}
.link-list li::before{content:"›";color:#555;margin-right:14px}
.social-list{list-style:none}
.social-list li{font-size:13px;color:#555;height:27px;display:flex;align-items:center;gap:10px}
.social-list i{width:13px;height:13px;background:#555;border-radius:2px;display:inline-block}
.news-text{font-size:12.5px;color:#666}
.footer-rule{left:88px;top:2501px;width:1024px;height:1px;background:#cfcfcf}
.copyright{left:0;width:1200px;top:2529px;text-align:center;font-size:13px;color:#555}
</style>
</head>
<body>

<!-- header -->
<div class="abs brand">tovarin</div>

<div class="abs contact-chip" style="left:724px">
  <div class="chip-icon">
    <svg width="20" height="20" viewBox="0 0 24 24"><path fill="#e0661a" d="M6.6 10.8c1.4 2.8 3.8 5.1 6.6 6.6l2.2-2.2c.3-.3.7-.4 1-.2 1.1.4 2.3.6 3.6.6.6 0 1 .4 1 1V20c0 .6-.4 1-1 1C10.6 21 3 13.4 3 4c0-.6.4-1 1-1h3.5c.6 0 1 .4 1 1 0 1.3.2 2.5.6 3.6.1.3 0 .7-.2 1z"/></svg>
  </div>
  <div><div class="chip-label">Call us</div><div class="chip-value">555-018-2946</div></div>
</div>
<div class="abs contact-chip" style="left:900px">
  <div class="chip-icon">
    <svg width="20" height="20" viewBox="0 0 24 24"><path fill="#e0661a" d="M3 5h18v14H3z"/><path fill="none" stroke="#fff" stroke-width="1.8" d="M3 6l9 7 9-7"/></svg>
  </div>
  <div><div class="chip-label">Mail us</div><div class="chip-value">info@tovarin-mail.com</div></div>
</div>

<nav class="abs main-nav">
  <a class="active">Home</a>
  <a>Who we are</a>
  <a>What we do</a>
  <a>What makes us different &#8964;</a>
  <a>Why it matters</a>
  <a>Candidate portal</a>
  <a>Contact us</a>
  <a>Blog</a>
</nav>

<!-- hero -->
<div class="abs hero" role="img" aria-label="Businessman in a suit holding a puzzle piece with people icons, tinted blue"></div>
<div class="abs hero-title-box"></div>
<div class="abs hero-title">Tovarin Business Solution</div>
<div class="abs hero-sub">We are IT recruiting and IT training company.</div>
<div class="abs hero-chevron">
  <svg width="16" height="16" viewBox="0 0 16 16"><path d="M3 3l5 4 5-4M3 8l5 4 5-4" fill="none" stroke="#fff" stroke-width="2"/></svg>
</div>

<div class="abs feature-photo" style="left:189px;top:468px;width:268px;height:268px;background:radial-gradient(circle at 50% 45%,#e7ecf1,#a9b8c6)" role="img" aria-label="Two business people shaking hands over a desk"></div>
<div class="abs feature-photo" style="left:442px;top:447px;width:316px;height:316px;background:radial-gradient(circle at 55% 45%,#c68b58,#7a5134 70%,#5b3d2a)" role="img" aria-label="Hand touching a cloud network diagram"></div>
<div class="abs feature-photo" style="left:741px;top:468px;width:268px;height:268px;background:radial-gradient(circle at 50% 45%,#d9b59a,#b06b4e 60%,#6f4a3b)" role="img" aria-label="Business charts and colourful 3D graphs"></div>

<svg class="abs mouse" style="left:312px;top:712px" viewBox="0 0 22 36"><rect x="1" y="1" width="20" height="34" rx="10" fill="#fff" stroke="#777" stroke-width="1.5"/><path d="M11 -6v16" stroke="#777" stroke-width="1.5"/></svg>
<svg class="abs mouse" style="left:589px;top:728px" viewBox="0 0 22 36"><rect x="1" y="1" width="20" height="34" rx="10" fill="#fff" stroke="#e0661a" stroke-width="1.5"/><path d="M11 -6v16" stroke="#e0661a" stroke-width="1.5"/></svg>
<svg class="abs mouse" style="left:862px;top:712px" viewBox="0 0 22 36"><rect x="1" y="1" width="20" height="34" rx="10" fill="#fff" stroke="#777" stroke-width="1.5"/><path d="M11 -6v16" stroke="#777" stroke-width="1.5"/></svg>

<div class="abs feature-caption" style="left:186px;top:791px"><div class="kicker">Customers view</div><div class="title">Candidate Portal</div></div>
<div class="abs feature-caption" style="left:460px;top:793px"><div class="kicker">About us</div><div class="title">Who we are</div></div>
<div class="abs feature-caption" style="left:735px;top:791px"><div class="kicker">Our Services</div><div class="title">What we do</div></div>

<!-- stats -->
<div class="abs stats" role="img" aria-label="Blue band with faint puzzle pieces background"></div>
<div class="abs stat" style="left:238px;top:977px">
  <svg width="86" height="76" viewBox="0 0 86 76"><polygon points="22,2 64,2 84,38 64,74 22,74 2,38" fill="none" stroke="#e0661a" stroke-width="2"/><circle cx="43" cy="32" r="6" fill="#fff"/><path d="M32 48c0-7 5-10 11-10s11 3 11 10z" fill="#fff"/></svg>
  <div class="num">6780</div><div class="label">Happy Clients</div>
</div>
<div class="abs stat" style="left:439px;top:977px">
  <svg width="86" height="76" viewBox="0 0 86 76"><polygon points="22,2 64,2 84,38 64,74 22,74 2,38" fill="none" stroke="#e0661a" stroke-width="2"/><path d="M30 30l13-7 13 7z M31 32h24v2H31z M33 35h3v10h-3z M39 35h3v10h-3z M45 35h3v10h-3z M51 35h3v10h-3z M30 46h26v3H30z" fill="#fff"/></svg>
  <div class="num">423</div><div class="label">Locations</div>
</div>
<div class="abs stat" style="left:633px;top:977px">
  <svg width="86" height="76" viewBox="0 0 86 76"><polygon points="22,2 64,2 84,38 64,74 22,74 2,38" fill="none" stroke="#e0661a" stroke-width="2"/><path d="M28 33l15-7 15 7-15 7z M35 37v7c5 4 11 4 16 0v-7l-8 4z" fill="#fff"/></svg>
  <div class="num">4000</div><div class="label">Awards</div>
</div>
<div class="abs stat" style="left:832px;top:977px">
  <svg width="86" height="76" viewBox="0 0 86 76"><polygon points="22,2 64,2 84,38 64,74 22,74 2,38" fill="none" stroke="#e0661a" stroke-width="2"/><circle cx="43" cy="30" r="5" fill="#fff"/><circle cx="33" cy="33" r="4" fill="#fff"/><circle cx="53" cy="33" r="4" fill="#fff"/><path d="M35 46c0-6 4-9 8-9s8 3 8 9z M26 45c0-5 3-7 7-7 2 0 3 1 4 1-2 2-3 4-3 6z M60 45c0-5-3-7-7-7-2 0-3 1-4 1 2 2 3 4 3 6z" fill="#fff"/></svg>
  <div class="num">9876</div><div class="label">Employees</div>
</div>

<!-- blog -->
<div class="abs blog"></div>
<div class="abs section-kicker" style="left:0;width:1200px;text-align:center;top:1245px">News</div>
<div class="abs section-title" style="left:0;width:1200px;text-align:center;top:1272px">Our Blog</div>

<article class="abs blog-card" style="left:98px">
  <div class="blog-photo" style="background:linear-gradient(135deg,#cfe3f2,#eef4f8 55%,#d8c7b8)" role="img" aria-label="Woman touching a virtual screen of people photos"></div>
  <div class="blog-head"><h3>Blog title here</h3><time>November 10,2016</time></div>
  <p>Lorem Ipsum as their default model text, and a search for&nbsp; still in their infancy.</p>
  <a class="read-more">READ MORE &gt;&gt;</a>
</article>
<article class="abs blog-card" style="left:445px">
  <div class="blog-photo" style="background:linear-gradient(180deg,#dfe2e4,#c9cccf)" role="img" aria-label="Businessman reading papers surrounded by floating photos"></div>
  <div class="blog-head"><h3>Blog title here</h3><time>November 11,2016</time></div>
  <p>Lorem Ipsum as their default model text, and a search for&nbsp; still in their infancy.</p>
  <a class="read-more">READ MORE &gt;&gt;</a>
</article>
<article class="abs blog-card" style="left:789px">
  <div class="blog-photo" style="background:linear-gradient(135deg,#f2f3f5,#c9d4e0 60%,#9aaabd)" role="img" aria-label="Smiling businesswoman with colleagues in a meeting"></div>
  <div class="blog-head"><h3>Blog title here</h3><time>December 01,2016</time></div>
  <p>Lorem Ipsum as their default model text, and a search for&nbsp; still in their infancy.</p>
  <a class="read-more">READ MORE &gt;&gt;</a>
</article>

<!-- callback -->
<div class="abs section-kicker" style="left:88px;top:1888px;font-size:14px">call back</div>
<div class="abs section-title" style="left:88px;top:1908px;font-size:26px;font-weight:500">Request a call back</div>
<div class="abs" style="left:88px;top:1964px;font-size:15px;color:#222">How can we help?</div>

<div class="abs field select" style="left:88px;top:2008px;width:239px">Business&nbsp; consulting <svg width="10" height="6" viewBox="0 0 10 6"><path d="M0 0h10L5 6z" fill="#333"/></svg></div>
<div class="abs field" style="left:335px;top:2008px;width:239px">Name</div>
<div class="abs field" style="left:88px;top:2051px;width:239px">E-mail</div>
<div class="abs field" style="left:335px;top:2051px;width:239px">Phone No</div>
<div class="abs btn" style="left:88px;top:2106px;width:105px;height:35px">Submit</div>

<div class="abs" style="left:598px;top:1996px;width:1px;height:140px;background:#d8d8d8"></div>
<div class="abs phone-box">
  <svg width="36" height="36" viewBox="0 0 24 24"><path fill="#e0661a" d="M6.6 10.8c1.4 2.8 3.8 5.1 6.6 6.6l2.2-2.2c.3-.3.7-.4 1-.2 1.1.4 2.3.6 3.6.6.6 0 1 .4 1 1V20c0 .6-.4 1-1 1C10.6 21 3 13.4 3 4c0-.6.4-1 1-1h3.5c.6 0 1 .4 1 1 0 1.3.2 2.5.6 3.6.1.3 0 .7-.2 1z"/></svg>
  <div><div class="small">Get Free Consulting&amp;Training</div><div class="big">555-018-2946</div></div>
</div>
<div class="abs hours">MONDAY - SATURDAY <span>/</span> <em>9:00 - 8:00</em></div>
<div class="abs" style="left:928px;top:2003px;width:190px;height:206px;background:linear-gradient(180deg,#e9e3df,#2a2a2e 45%,#1b1b1f);border-radius:40% 40% 0 0" role="img" aria-label="Businesswoman in a black suit presenting"></div>

<!-- footer -->
<footer class="abs footer" role="img" aria-label="Light grey wood texture background"></footer>

<h4 class="abs" style="left:88px;top:2264px;font-size:19px;font-weight:500;color:#222">GET IN TOUCH</h4>
<div class="abs" style="left:88px;top:2310px;display:flex;flex-direction:column;gap:18px">
  <div class="touch-item">
    <div class="touch-icon"><svg width="14" height="16" viewBox="0 0 14 18"><path d="M7 0C3 0 0 3 0 7c0 5 7 11 7 11s7-6 7-11c0-4-3-7-7-7zm0 9.5A2.5 2.5 0 117 4.5a2.5 2.5 0 010 5z" fill="#0b5ca0"/></svg></div>
    <div class="touch-text">34 gh,Lorem ipsum<br>dolor</div>
  </div>
  <div class="touch-item">
    <div class="touch-icon"><svg width="16" height="16" viewBox="0 0 24 24"><path fill="#0b5ca0" d="M6.6 10.8c1.4 2.8 3.8 5.1 6.6 6.6l2.2-2.2c.3-.3.7-.4 1-.2 1.1.4 2.3.6 3.6.6.6 0 1 .4 1 1V20c0 .6-.4 1-1 1C10.6 21 3 13.4 3 4c0-.6.4-1 1-1h3.5c.6 0 1 .4 1 1 0 1.3.2 2.5.6 3.6.1.3 0 .7-.2 1z"/></svg></div>
    <div class="touch-text"><strong>CALL US</strong>555-018-2946</div>
  </div>
  <div class="touch-item">
    <div class="touch-icon"><svg width="16" height="16" viewBox="0 0 24 24"><path fill="#0b5ca0" d="M3 5h18v14H3z"/><path fill="none" stroke="#fff" stroke-width="1.8" d="M3 6l9 7 9-7"/></svg></div>
    <div class="touch-text"><strong>MAIL US</strong>info@tovarin-mail.com</div>
  </div>
</div>

<h4 class="abs" style="left:366px;top:2264px;font-size:19px;font-weight:500;color:#222">QUICK LINKS</h4>
<ul class="abs link-list" style="left:366px;top:2305px">
  <li>Home</li><li>who we are</li><li>what we do</li><li>what makes us different</li><li>why it matters</li><li>candidate portal</li><li>contact us</li><li>Blog</li>
</ul>

<h4 class="abs" style="left:593px;top:2264px;font-size:19px;font-weight:500;color:#222">FOLLOW US</h4>
<ul class="abs social-list" style="left:593px;top:2300px">
  <li><i></i>Facelink</li><li><i></i>Chirper</li><li><i></i>Vidstream</li><li><i></i>Circleplus</li><li><i></i>Snapgram</li>
</ul>

<h4 class="abs" style="left:803px;top:2264px;font-size:19px;font-weight:500;color:#222">NEWSLETTER</h4>
<div class="abs news-text" style="left:803px;top:2303px">Sign up for newsletters, events and the promotions</div>
<div class="abs field" style="left:803px;top:2336px;width:310px;height:38px;border-radius:4px;border-color:#d5d5d5;font-style:italic;font-size:12px">E-mail Address</div>
<div class="abs btn" style="left:803px;top:2388px;width:104px;height:38px;background:var(--blue);border-radius:6px">Subscribe</div>

<div class="abs footer-rule"></div>
<div class="abs copyright">@copyright 2016 Tovarin Business Solution.All Rights Reserved</div>

</body>
</html>
```